holloway paving service

Needs to have phone number 0418259730 and email markholloway@brightmail.com.au.
ABN 62318470915
name mark holloway

For all your concreting solutions
Excavation
Exposed & colour concrete
House & shed slabs
Driveways
Landing & steps

Contact Information for Business Card

ph 0418259730
email markholloway@brightmail.com.au.
ABN 62318470915
name mark holloway

```html
<!DOCTYPE html>
<html lang="en">
<head>
<meta charset="utf-8">
<title>Holloway Paving Service – Business Card</title>
<link rel="stylesheet" href="https://fonts.googleapis.com/css2?family=Roboto:wght@400;500&family=Roboto+Condensed:wght@700&family=Montserrat:wght@500;600&display=swap">
<style>
  :root {
    --backdrop: #2e2e2e;
    --card-front: #f4f4f4;
    --card-back: #6b6b6b;
    --orange: #f26a21;
    --grey-line: #6b6b6b;
    --ink: #4a4a4a;
    --white: #ffffff;
  }
  * { margin: 0; padding: 0; box-sizing: border-box; }
  html, body { width: 1200px; height: 960px; overflow: hidden; }
  body {
    background: var(--backdrop);
    position: relative;
    font-family: "Roboto", Arial, sans-serif;
  }
  .card {
    position: absolute;
    width: 600px;
    height: 342px;
    box-shadow: 0 3px 8px rgba(0,0,0,0.45);
    overflow: hidden;
  }
  .card-front { left: 322px; top: 110px; background: var(--card-front); }
  .card-back { left: 320px; top: 493px; background: var(--card-back); }

  /* brand lockup */
  .brand { position: absolute; left: 53px; top: 121px; display: flex; align-items: center; }
  .brand-mark { width: 26px; height: 26px; background: var(--orange); }
  .brand-divider { width: 2px; height: 66px; background: var(--orange); margin: 0 6px 0 48px; }
  .brand-name {
    font-family: "Montserrat", Arial, sans-serif;
    font-weight: 600;
    color: var(--orange);
    text-align: center;
    width: 166px;
  }
  .brand-line1 { font-size: 13px; line-height: 15px; }
  .brand-line2, .back-line2 {
    display: flex; align-items: center; justify-content: center;
    letter-spacing: 1.5px;
  }
  .brand-line2 { font-size: 10.5px; line-height: 12px; color: var(--ink); }
  .brand-line2::before, .brand-line2::after,
  .back-line2::before, .back-line2::after {
    content: ""; flex: 1; height: 1.5px; background: currentColor; margin: 0 6px;
  }
  .brand-phone { font-size: 11px; line-height: 12px; letter-spacing: 1.2px; }

  /* contact */
  .contact { position: absolute; left: 329px; top: 87px; color: var(--ink); }
  .person-name {
    font-family: "Roboto Condensed", Arial, sans-serif;
    font-weight: 700;
    font-size: 22px;
    color: var(--orange);
    margin-bottom: 11px;
  }
  .contact-row { display: flex; align-items: center; font-size: 14px; line-height: 19px; }
  .contact-row svg { width: 12px; height: 12px; margin-right: 9px; fill: var(--orange); }
  .abn { font-size: 14px; margin-top: 11px; }

  /* service band */
  .band-edge { position: absolute; left: 0; top: 276px; width: 600px; height: 66px; }
  .service-band {
    position: absolute; left: 0; top: 295px; width: 600px;
    color: var(--white);
    font-size: 14px;
    line-height: 18px;
    text-align: center;
  }

  /* back */
  .back-details {
    position: absolute; left: 327px; top: 234px; width: 240px;
    text-align: center; color: var(--white);
    font-family: "Montserrat", Arial, sans-serif;
  }
  .back-name { font-weight: 600; font-size: 17px; line-height: 19px; }
  .back-line2 { font-weight: 500; font-size: 13px; line-height: 15px; letter-spacing: 2px; }
  .back-phone { font-size: 14px; font-weight: 500; line-height: 16px; letter-spacing: 1px; }
  .back-web { font-size: 13px; letter-spacing: 3px; margin-top: 3px; font-weight: 500; }
</style>
</head>
<body>
  <section class="card card-front">
    <div class="brand">
      <div class="brand-mark"></div>
      <div class="brand-divider"></div>
      <div class="brand-name">
        <p class="brand-line1">HOLLOWAY PAVING</p>
        <p class="brand-line2">SERVICE</p>
        <p class="brand-phone">0418259730</p>
      </div>
    </div>

    <div class="contact">
      <h1 class="person-name">MARK HOLLOWAY</h1>
      <p class="contact-row">
        <svg viewBox="0 0 24 24" aria-hidden="true"><path d="M6.6 10.8a15.1 15.1 0 0 0 6.6 6.6l2.2-2.2c.3-.3.7-.4 1-.2 1.1.4 2.3.6 3.6.6.6 0 1 .4 1 1V20c0 .6-.4 1-1 1A17 17 0 0 1 3 4c0-.6.4-1 1-1h3.5c.6 0 1 .4 1 1 0 1.3.2 2.5.6 3.6.1.3 0 .7-.2 1z"/></svg>
        0418259730
      </p>
      <p class="contact-row">
        <svg viewBox="0 0 24 24" aria-hidden="true"><path d="M2 5h20v14H2z"/><path d="M3 6l9 7 9-7" fill="none" stroke="#f4f4f4" stroke-width="1.6"/></svg>
        markholloway@brightmail.com.au
      </p>
      <p class="contact-row">
        <svg viewBox="0 0 24 24" aria-hidden="true"><circle cx="12" cy="12" r="10"/><path d="M2 12h20M12 2c3 3 3 17 0 20M12 2c-3 3-3 17 0 20" fill="none" stroke="#f4f4f4" stroke-width="1.4"/></svg>
        www.hollowaypaving.com.au
      </p>
      <p class="abn">ABN 62318470915</p>
    </div>

    <svg class="band-edge" viewBox="0 0 600 66" aria-hidden="true">
      <polyline points="0,5 70,5 89,22 108,5 600,5" fill="none" stroke="var(--grey-line)" stroke-width="3.5"/>
      <polygon points="0,10 68,10 89,29 110,10 600,10 600,66 0,66" fill="var(--orange)"/>
    </svg>
    <div class="service-band">
      <p>Excavation | Exposed &amp; colour concrete</p>
      <p>House &amp; shed slabs | Driveways | Landing &amp; steps</p>
    </div>
  </section>

  <section class="card card-back">
    <div class="back-details">
      <p class="back-name">HOLLOWAY PAVING</p>
      <p class="back-line2">SERVICE</p>
      <p class="back-phone">0418259730</p>
      <p class="back-web">www.hollowaypaving.com.au</p>
    </div>
  </section>
</body>
</html>
```